Brookvale Building Company - advertisement poster

I am looking to print some canvas signs to advertise my general contracting company, Brookvale Building Company. The sign will measure 6' long x 3' high so the size should match that ratio. I already have a logo icon, which is the Letter 'B' and some trees that I would like to incorporate, see attached. I would also like the to have the following information listed:
1) phone number: 831-555-0172
2) email: brookvalebuildingcompany@mailnest.example
3) website: brookvalebuildingcompany.example
4) Lic#4826130
5) I want to use this text: "BUILD WITH THE B-CREW!"

The ad should be relatively simple and clean. Black and Green are my company colors. I am open to creative ideas!

Target Market(s)

People looking to renovate their homes

Industry/Entity Type

Construction

Colors
59FF00
82FF00
B8FF75
E3FFCB
F4FFEA

Requirements
Must have
• Must have my company logo
Should not have
• No photos or complex graphics

```html
<!DOCTYPE html>
<html lang="en">
<head>
<meta charset="utf-8">
<title>Brookvale Building Company – Sign</title>
<link rel="stylesheet" href="https://fonts.googleapis.com/css2?family=Michroma&family=Poppins:wght@600;700;800&display=swap">
<style>
  :root {
    --backdrop: #c8c8c8;
    --sign-top: #000000;
    --sign-bottom: #1c1c1c;
    --brand-green: #6db344;
    --white: #ffffff;
    --ink: #111111;
    --rule: #444444;
  }
  html, body {
    margin: 0;
    width: 1200px;
    height: 1033px;
    overflow: hidden;
    background: var(--backdrop);
  }
  .sign {
    position: absolute;
    left: 98px;
    top: 266px;
    width: 1004px;
    height: 501px;
    display: block;
  }
  .headline { font-family: "Michroma", sans-serif; }
  .headline--green { fill: var(--brand-green); }
  .headline--white { fill: var(--white); font-weight: 700; }
  .brand-name { font-family: "Poppins", sans-serif; font-weight: 700; fill: var(--white); letter-spacing: 1px; }
  .phone-number { font-family: "Poppins", sans-serif; font-weight: 700; fill: var(--white); }
  .contact-line { font-family: "Poppins", sans-serif; font-weight: 600; fill: var(--white); letter-spacing: 0.6px; }
  .license-label, .license-number { font-family: "Poppins", sans-serif; font-weight: 700; fill: var(--ink); letter-spacing: 1px; }
</style>
</head>
<body>
<svg class="sign" viewBox="0 0 1004 501" xmlns="http://www.w3.org/2000/svg" role="img" aria-label="Brookvale Building Company sign">
  <!-- background bands -->
  <rect class="band-top" x="0" y="0" width="1004" height="262" fill="var(--sign-top)"/>
  <rect class="band-bottom" x="0" y="262" width="1004" height="239" fill="var(--sign-bottom)"/>

  <!-- brand block -->
  <g class="brand">
    <rect class="brand-mark" x="146" y="72" width="48" height="48" fill="var(--brand-green)"/>
    <text class="brand-name" x="170" y="152" font-size="21" text-anchor="middle">BROOKVALE</text>
    <text class="brand-name" x="170" y="176" font-size="12.5" text-anchor="middle" letter-spacing="2.6">BUILDING COMPANY</text>
  </g>

  <line class="divider" x1="300" y1="39" x2="300" y2="188" stroke="var(--rule)" stroke-width="2"/>

  <!-- headline -->
  <text class="headline headline--green" x="329" y="94" font-size="72" textLength="603" lengthAdjust="spacingAndGlyphs">BUILD WITH</text>
  <text class="headline headline--white" x="329" y="187" font-size="100" textLength="603" lengthAdjust="spacingAndGlyphs" stroke="var(--white)" stroke-width="3">B- CREW</text>

  <!-- phone banner -->
  <polygon class="phone-banner" points="72,210 933,210 868,309 124,309" fill="var(--brand-green)"/>
  <g class="phone-icon">
    <circle cx="175" cy="260" r="30" fill="var(--sign-top)"/>
    <path d="M164 245 l6 -3 l6 10 l-4 4 q3 7 10 11 l4 -4 l10 6 l-3 6 q-4 4 -12 0 q-14 -8 -20 -20 q-2 -7 3 -10 z" fill="var(--white)"/>
    <path d="M178 246 q8 2 10 10" fill="none" stroke="var(--white)" stroke-width="2.5" stroke-linecap="round"/>
    <path d="M179 238 q15 3 17 18" fill="none" stroke="var(--white)" stroke-width="2.5" stroke-linecap="round"/>
  </g>
  <text class="phone-number" x="223" y="290" font-size="88" textLength="608" lengthAdjust="spacingAndGlyphs">831-555-0172</text>

  <!-- contact lines -->
  <g class="email-icon">
    <rect x="151" y="341" width="22" height="16" fill="var(--brand-green)"/>
    <path d="M151 341 l11 9 l11 -9" fill="none" stroke="var(--sign-bottom)" stroke-width="1.8"/>
  </g>
  <text class="contact-line" x="182" y="357" font-size="25.5" textLength="671" lengthAdjust="spacingAndGlyphs">brookvalebuildingcompany@mailnest.example</text>

  <g class="web-icon" fill="none" stroke="var(--brand-green)" stroke-width="2">
    <circle cx="222" cy="386" r="11"/>
    <ellipse cx="222" cy="386" rx="5" ry="11"/>
    <line x1="211" y1="386" x2="233" y2="386"/>
  </g>
  <text class="contact-line" x="244" y="395" font-size="27" textLength="538" lengthAdjust="spacingAndGlyphs">brookvalebuildingcompany.example</text>

  <!-- license tag -->
  <polygon class="license-tag-label" points="277,430 496,430 471,467 301,467" fill="var(--brand-green)"/>
  <polygon class="license-tag-number" points="496,430 726,430 701,467 478,467" fill="var(--white)"/>
  <text class="license-label" x="393" y="460" font-size="26" text-anchor="middle">LICENSE</text>
  <text class="license-number" x="600" y="460" font-size="27" text-anchor="middle">#4826130</text>
</svg>
</body>
</html>
```